Brightline Energy Product Distribution Brochure

We are looking to have our current brochure for our customers completely redesigned...the idea is to present the relevant information in an attractive way . Our website is brightlineenergyco.example where you can find more information about us. We have included a file with a rough idea of the page order and what each should include but feel free to adapt based on design. The example provided is only for context and doesnt have to be maintained. We will be using the brochure both digitally and in print form. As long as it reads easily and is eye catching, the design can be horizontal or vertical.Final deliverable should be indesign file.

"Our Brands" page: should be limited to one page (space being enough) where it has the header for each one (for example diesel generators) space for one or two lines of text and then the corresponding logos for each of the five categories
Updates

For those asking: the "our brands" page should be a single page layout where there is a header with the corresponding section and space for maybe one line of text followed by the two logos for that category. Each of the product pages should be similar in fashion to the one in the document attached: a photo of the product with some white space and space for the text to be included. We will be posting additional examples today

Target Market(s)

We want to present it to customers both digitally and in print so they can see our products

Industry/Entity Type

Power Generation

Font styles to use
Serif

Requirements
Must have
• Eye catching and able to present the information in a presentable fashion. Rest is up to you.
Nice to have
• Should incorporate the colors of our logo but can also add other depending on design

```html
<!DOCTYPE html>
<html lang="en">
<head>
<meta charset="utf-8">
<title>Brightline Energy – Distributor Program Guide Covers</title>
<link href="https://fonts.googleapis.com/css2?family=Archivo+Black&family=Roboto:wght@400;500;700&family=Work+Sans:wght@400&display=swap" rel="stylesheet">
<style>
  :root {
    --board-light: #cfd0d2;
    --board-dark: #7c7d80;
    --ink: #3d3b3c;
    --stripe-dark: #4a4546;
    --brand-yellow: #f7c21a;
    --paper: #ffffff;
    --label: #4a4a4c;
  }
  html, body { margin: 0; padding: 0; overflow: hidden; }
  body { width: 1200px; height: 870px; }
  .board {
    position: relative;
    width: 1200px; height: 870px;
    background: var(--board-light);
    overflow: hidden;
  }
  .board-band { position: absolute; inset: 0; }
  .option-label {
    position: absolute; top: 88px; margin: 0;
    font: 400 13.5px/1 "Work Sans", sans-serif;
    letter-spacing: 0.04em; color: var(--label);
  }
  .cover {
    position: absolute; top: 118px;
    width: 509px; height: 652px;
    box-shadow: 0 7px 0 #4e4c4d;
  }
  .cover svg { display: block; width: 100%; height: 100%; }
  .title-heavy { font-family: "Archivo Black", sans-serif; }
  .subtitle { font-family: "Roboto", sans-serif; font-weight: 500; }
  .address { font-family: "Roboto", sans-serif; font-size: 10.5px; fill: var(--ink); }
  .phone { font-family: "Roboto", sans-serif; font-weight: 700; font-size: 10.5px; fill: var(--brand-yellow); }
  .brand-name { font-family: "Roboto", sans-serif; font-weight: 400; font-size: 21px; fill: var(--ink); letter-spacing: 0.06em; }
</style>
</head>
<body>
<main class="board">
  <svg class="board-band" width="1200" height="870" viewBox="0 0 1200 870" aria-hidden="true">
    <polygon points="0,566 1200,179 1200,870 0,870" fill="var(--board-dark)"/>
  </svg>

  <p class="option-label" style="left:77px">COVER OPTION 1</p>
  <p class="option-label" style="left:615px">COVER OPTION 2</p>

  <svg width="0" height="0" style="position:absolute" aria-hidden="true">
    <defs>
      <linearGradient id="plant-tones" x1="0" y1="0" x2="0.3" y2="1">
        <stop offset="0" stop-color="#c9a55a"/>
        <stop offset="0.35" stop-color="#a8782f"/>
        <stop offset="0.7" stop-color="#5e4527"/>
        <stop offset="1" stop-color="#3a2c20"/>
      </linearGradient>
      <linearGradient id="machine-tones" x1="0" y1="0" x2="1" y2="1">
        <stop offset="0" stop-color="#d8e0ea"/>
        <stop offset="0.6" stop-color="#7f94ae"/>
        <stop offset="1" stop-color="#c86a2a"/>
      </linearGradient>
      <linearGradient id="pipework-tones" x1="0" y1="0" x2="1" y2="1">
        <stop offset="0" stop-color="#dfe3e6"/>
        <stop offset="0.55" stop-color="#8a9099"/>
        <stop offset="1" stop-color="#2c3850"/>
      </linearGradient>
      <filter id="title-shadow" x="-5%" y="-20%" width="110%" height="140%">
        <feDropShadow dx="1" dy="2" stdDeviation="1.5" flood-color="#000" flood-opacity="0.7"/>
      </filter>
      <clipPath id="page-clip"><rect width="611" height="783"/></clipPath>
    </defs>
  </svg>

  <!-- Cover option 1 -->
  <section class="cover" style="left:77px" aria-label="Cover option 1">
    <svg viewBox="0 0 611 783">
      <g clip-path="url(#page-clip)">
        <rect width="611" height="783" fill="var(--paper)"/>
        <polygon class="cover-photo" role="img" aria-label="Industrial power plant at dusk with glowing lights"
          points="0,0 611,0 611,250 200,661 0,461" fill="url(#plant-tones)"/>
        <polyline points="-10,475 198,683 630,251" fill="none" stroke="var(--stripe-dark)" stroke-width="22"/>
        <polyline points="-10,405 260,675 630,305" fill="none" stroke="var(--brand-yellow)" stroke-width="18"/>
        <polygon role="img" aria-label="Generator machinery detail" points="448,368 528,448 448,528 368,448" fill="url(#machine-tones)"/>
        <polygon role="img" aria-label="Engineers at pipework installation" points="343,478 423,558 343,638 263,558" fill="url(#pipework-tones)"/>

        <g filter="url(#title-shadow)" fill="#fff">
          <text class="title-heavy" x="50" y="110" font-size="41">DISTRIBUTOR</text>
          <text class="title-heavy" x="50" y="153" font-size="41">PROGRAM GUIDE</text>
          <text class="subtitle" x="50" y="217" font-size="27" letter-spacing="0.5">DIESEL GENERATORS</text>
          <text class="subtitle" x="50" y="254" font-size="27" letter-spacing="0.5">ALTERNATORS &amp; PARTS</text>
        </g>
        <rect x="50" y="174" width="82" height="1.5" fill="#fff"/>

        <text class="address" x="43" y="715">Brightline Energy Limited, Inc.</text>
        <text class="address" x="43" y="728">4120 Harbor Point Drive</text>
        <text class="address" x="43" y="741">Tampa, FL 33602, USA</text>
        <text class="phone" x="43" y="761">1-800-555-0142</text>

        <rect x="450" y="648" width="34" height="34" fill="var(--brand-yellow)"/>
        <text class="brand-name" x="559" y="738" text-anchor="end">BRIGHTLINE ENERGY</text>
      </g>
    </svg>
  </section>

  <!-- Cover option 2 -->
  <section class="cover" style="left:615px" aria-label="Cover option 2">
    <svg viewBox="0 0 611 783">
      <g clip-path="url(#page-clip)">
        <rect width="611" height="783" fill="var(--paper)"/>
        <polygon class="cover-photo" role="img" aria-label="Industrial power plant at dusk with glowing lights"
          points="0,340 200,168 330,0 611,0 611,250 200,661 0,461" fill="url(#plant-tones)"/>
        <polygon class="header-panel" points="0,0 340,0 318,33 611,33 519,168 0,168" fill="var(--paper)"/>
        <polygon points="340,0 372,0 350,33 318,33" fill="var(--stripe-dark)"/>
        <polygon points="382,0 414,0 392,33 360,33" fill="var(--brand-yellow)"/>
        <polygon points="0,168 205,168 0,330" fill="var(--paper)"/>
        <line x1="-10" y1="362" x2="240" y2="160" stroke="var(--brand-yellow)" stroke-width="14"/>

        <polyline points="-10,475 198,683 630,251" fill="none" stroke="var(--stripe-dark)" stroke-width="22"/>
        <polyline points="-10,405 260,675 630,305" fill="none" stroke="var(--brand-yellow)" stroke-width="18"/>
        <polygon role="img" aria-label="Generator machinery detail" points="448,368 528,448 448,528 368,448" fill="url(#machine-tones)"/>
        <polygon role="img" aria-label="Engineers at pipework installation" points="343,478 423,558 343,638 263,558" fill="url(#pipework-tones)"/>

        <text class="title-heavy" x="49" y="88" font-size="29.5" fill="var(--ink)">DISTRIBUTOR PROGRAM GUIDE</text>
        <rect x="49" y="106" width="82" height="3" fill="var(--brand-yellow)"/>
        <text class="subtitle" x="49" y="140" font-size="19.5" fill="var(--ink)" letter-spacing="0.4">DIESEL GENERATORS ALTERNATORS &amp; PARTS</text>

        <text class="address" x="43" y="715">Brightline Energy Limited, Inc.</text>
        <text class="address" x="43" y="728">4120 Harbor Point Drive</text>
        <text class="address" x="43" y="741">Tampa, FL 33602, USA</text>
        <text class="phone" x="43" y="761">1-800-555-0142</text>

        <rect x="450" y="648" width="34" height="34" fill="var(--brand-yellow)"/>
        <text class="brand-name" x="559" y="738" text-anchor="end">BRIGHTLINE ENERGY</text>
      </g>
    </svg>
  </section>
</main>
</body>
</html>
```